Event Center Website

We need a new website design for an upscale event center in Reno, Nevada. The building hosts everything from weddings to corporate events to funerals and it competitively more expensive. The overall look and feel is consistent with a Lake Tahoe aesthetic. The current site can be viewed at www.themaplehallevents.com. They are looking for a major upgrade. A sample site they like is www.cliffsidelodgestay.com. We have new photography available (some attached). The site should be very visual. A site map is attached as well for direction on what elements the site should include as well as labels for navigation. I am looking for a home page and sample interior page. Any questions, let me know. Thanks.
Updates

I have added some photography of the center itself for use rather than stock photography. Thanks!

Target Market(s)

Brides, professionals, high-income

Industry/Entity Type

Building

Requirements
Must have
• See site map

```html
<!DOCTYPE html>
<html lang="en">
<head>
<meta charset="utf-8">
<title>The Maple Hall — Reno Special Events Center</title>
<link href="https://fonts.googleapis.com/css2?family=Great+Vibes&family=Open+Sans:wght@400;600;700&display=swap" rel="stylesheet">
<style>
  :root {
    --bar: #000000;
    --footer: #050505;
    --white: #ffffff;
    --nav-text: #d8d8d8;
    --muted: #c9c9c9;
    --logo-bg: #5a2f17;
    --hero-deep: #0b1030;
    --hero-blue: #1d2a78;
    --hero-violet: #3a2460;
    --hero-glow: #5661b8;
  }
  * { box-sizing: border-box; margin: 0; padding: 0; }
  html, body { width: 1200px; height: 728px; overflow: hidden; background: var(--bar); }
  body { font-family: "Open Sans", Arial, sans-serif; color: var(--white); position: relative; }

  .site-header {
    position: absolute; top: 0; left: 0; width: 1200px; height: 56px;
    background: var(--bar);
  }
  .brand {
    position: absolute; left: 7px; top: 7px; width: 129px; height: 41px;
    background: var(--logo-bg); display: flex; align-items: center; justify-content: center; gap: 6px;
  }
  .brand-dot { width: 8px; height: 8px; background: var(--white); border-radius: 50%; }
  .brand-name { font-size: 13px; font-weight: 600; color: var(--white); letter-spacing: 0.3px; }

  .main-nav {
    position: absolute; right: 72px; top: 0; height: 56px;
    display: flex; align-items: center; font-size: 11px; color: var(--nav-text);
  }
  .main-nav a { color: var(--nav-text); text-decoration: none; white-space: nowrap; }
  .main-nav .sep { margin: 0 11px; }
  .menu-toggle { position: absolute; right: 20px; top: 17px; }

  .hero {
    position: absolute; top: 56px; left: 0; width: 1200px; height: 603px;
    background:
      radial-gradient(ellipse at 55% 45%, var(--hero-glow) 0%, transparent 45%),
      radial-gradient(ellipse at 20% 30%, var(--hero-violet) 0%, transparent 50%),
      linear-gradient(180deg, var(--hero-blue) 0%, var(--hero-deep) 100%);
  }
  .slider-arrow { position: absolute; top: 256px; }
  .slider-arrow.prev { left: 52px; }
  .slider-arrow.next { right: 52px; }

  .hero-title {
    position: absolute; top: 260px; left: 0; width: 1200px; text-align: center;
    font-family: "Great Vibes", cursive; font-size: 52px; line-height: 60px; font-weight: 400;
    white-space: nowrap;
  }
  .hero-subtitle {
    position: absolute; top: 341px; left: 0; width: 1200px; height: 16px;
    display: flex; align-items: center; justify-content: center; gap: 8px;
    font-size: 11px; letter-spacing: 5px;
  }
  .hero-subtitle .rule { width: 26px; height: 1px; background: var(--white); }

  .cta { position: absolute; }
  .cta h2 { font-size: 15px; line-height: 20px; font-weight: 600; text-transform: uppercase; margin-bottom: 7px; }
  .cta p { font-size: 13.5px; line-height: 21px; }
  .cta .btn {
    display: inline-block; margin-top: 13px; border: 2px solid var(--white);
    font-size: 10px; line-height: 12px; font-weight: 700; text-transform: uppercase;
    padding: 7px 18px; color: var(--white); text-decoration: none;
  }
  .cta.mailing { left: 99px; top: 471px; }
  .cta.appointment { right: 100px; top: 446px; text-align: right; }

  .site-footer {
    position: absolute; top: 659px; left: 0; width: 1200px; height: 69px;
    background: var(--footer); font-family: Arial, Helvetica, sans-serif; font-size: 11px; color: var(--muted);
  }
  .legal { position: absolute; left: 100px; top: 27px; display: flex; gap: 14px; }
  .social { position: absolute; right: 100px; top: 17px; display: flex; align-items: center; gap: 8px; }
  .social span { margin-right: 6px; }
  .social-dot { width: 34px; height: 34px; border: 1.5px solid #8a8a8a; border-radius: 50%; }
</style>
</head>
<body>
  <header class="site-header">
    <div class="brand"><span class="brand-dot"></span><span class="brand-name">The Maple Hall</span></div>
    <nav class="main-nav">
      <a href="#">About Us</a><span class="sep">/</span>
      <a href="#">Gallery</a><span class="sep">/</span>
      <a href="#">Weddings</a><span class="sep">/</span>
      <a href="#">Meetings</a><span class="sep">/</span>
      <a href="#">Other Events</a><span class="sep">/</span>
      <a href="#">Catering</a><span class="sep">/</span>
      <a href="#">Menus</a><span class="sep">/</span>
      <a href="#">FAQs</a><span class="sep">/</span>
      <a href="#">Testimonials</a><span class="sep">/</span>
      <a href="#">Contact Us</a><span class="sep">/</span>
      <a href="#">Schedule an Appointment</a>
    </nav>
    <svg class="menu-toggle" width="25" height="22" viewBox="0 0 25 22" aria-label="Menu">
      <rect x="0" y="1" width="25" height="3.5" rx="1.5" fill="#bdbdbd"/>
      <rect x="0" y="9" width="25" height="3.5" rx="1.5" fill="#bdbdbd"/>
      <rect x="0" y="17" width="25" height="3.5" rx="1.5" fill="#bdbdbd"/>
    </svg>
  </header>

  <section class="hero" role="img" aria-label="Photo of friends enjoying drinks in a blue-lit lounge at the events center">
    <svg class="slider-arrow prev" width="14" height="44" viewBox="0 0 14 44"><polyline points="13,1 1,22 13,43" fill="none" stroke="rgba(255,255,255,0.5)" stroke-width="1"/></svg>
    <svg class="slider-arrow next" width="14" height="44" viewBox="0 0 14 44"><polyline points="1,1 13,22 1,43" fill="none" stroke="rgba(255,255,255,0.5)" stroke-width="1"/></svg>

    <h1 class="hero-title">The Maple Hall is Reno’s newest</h1>
    <div class="hero-subtitle"><span class="rule"></span>MOST ELEGANT SPECIAL EVENTS CENTER<span class="rule"></span></div>

    <div class="cta mailing">
      <h2>Join Our Mailing List</h2>
      <p>Get our recent updates through your email id</p>
      <a class="btn" href="#">Subscribe Now</a>
    </div>
    <div class="cta appointment">
      <h2>Schedule an Appointment</h2>
      <p>The Maple Hall is Reno's newest, most elegant<br>special events center.</p>
      <a class="btn" href="#">Get an Appointment</a>
    </div>
  </section>

  <footer class="site-footer">
    <div class="legal">
      <span>© Copyright 2014. The Maple Hall. All Rights Reserved.</span>
      <span>Terms &amp; Conditions</span><span>/</span><span>Privacy policy</span>
    </div>
    <div class="social">
      <span>Connect with our social network :</span>
      <div class="social-dot"></div>
      <div class="social-dot"></div>
    </div>
  </footer>
</body>
</html>
```